Design an Office Mural for Electrical Engineering Company

We have a blank wall in our commercial office space that we would love to decorate with custom wallpaper. For this purpose, we are seeking a design to have printed as wallpaper and hung on the wall.

The design should include typography with our slogan "elevate your expectations". It is important that the design uses orange, charcoal and dark blue but other colours can also be incorporated. We want this graphic to appeal to our workforce of young, fun and intelligent men. You may like to include elements of engineering, electrical and automation in your graphic.

I have attached our logo for reference. You can choose whether or not to incorporate design elements from the logo but please DO NOT cut and paste the logo onto your design. I have attached examples of other murals that we like. Please use these as a reference for the style of your work.

The wall dimensions are 2m wide by 2.6m tall. Unfortunately we don't have a photo of the wall as it is under construction.

Target Market(s)

Young - Middle Aged Men, Tradesmen, Business People, Industrial Clients

Industry/Entity Type

Electrical engineering, factory automation, industrial maintenance

Colors
0054AA
0677BA
7BADD7
CADEEF
E8F1F8
F0912C
F2A743
F7CA91
FBE8D2
FDF5EE

Requirements
Must have
• Company colours (orange and charcoal), slogan "elevate your expectations"
Nice to have
• Hand lettering and illustration
Should not have
• The logo copy and pasted on the design. Stock images or any photographs.

```html
<!DOCTYPE html>
<html lang="en">
<head>
<meta charset="utf-8">
<title>Elevate Your Expectations – Office Mural</title>
<link rel="stylesheet" href="https://fonts.googleapis.com/css2?family=Bebas+Neue&display=swap">
<style>
  :root {
    --orange: #fda600;
    --orange-soft: #fdb92a;
    --blue-deep: #0041b3;
    --blue-mid: #0677d9;
    --blue-bright: #0a84f5;
    --blue-sky: #4fb3ff;
    --bulb-bg: #eaf9fc;
    --network-bg: #dba86c;
    --white: #ffffff;
  }
  html, body {
    margin: 0;
    padding: 0;
    overflow: hidden;
    background: var(--orange);
  }
  .mural {
    width: 923px;
    height: 1200px;
    position: relative;
    overflow: hidden;
    background: var(--orange);
  }
  .mural svg { display: block; }
  .slogan {
    font-family: "Bebas Neue", "Oswald", sans-serif;
    fill: var(--white);
    letter-spacing: 0;
  }
</style>
</head>
<body>
<main class="mural">
  <svg width="923" height="1200" viewBox="0 0 923 1200" xmlns="http://www.w3.org/2000/svg">
    <defs>
      <linearGradient id="column-fill" x1="0" y1="0" x2="1" y2="0">
        <stop offset="0" stop-color="#0a74e0"/>
        <stop offset="0.45" stop-color="#0566d8"/>
        <stop offset="1" stop-color="#0047b8"/>
      </linearGradient>
    </defs>

    <!-- soft halo behind the lettering -->
    <circle class="halo" cx="494" cy="401" r="363" fill="var(--orange-soft)" opacity="0.75"/>

    <!-- icon badges -->
    <circle class="badge badge-network" cx="142" cy="184" r="104" fill="var(--network-bg)" role="img" aria-label="Network node icon: hub circle with connected points"/>
    <g class="badge badge-idea" fill="none" stroke="var(--white)" stroke-width="1">
      <path d="M465 90 A160 160 0 0 1 770 110"/>
      <circle cx="612" cy="166" r="130" opacity="0.8"/>
    </g>
    <circle class="badge badge-idea-fill" cx="612" cy="166" r="113" fill="var(--bulb-bg)" role="img" aria-label="Lightbulb idea icon"/>
    <circle class="badge-ring" cx="795" cy="293" r="166" fill="none" stroke="var(--blue-deep)" stroke-width="1"/>

    <!-- extruded lettering columns -->
    <polygon class="columns" points="40,325 575,110 575,520 700,470 885,555 885,1200 40,1200" fill="url(#column-fill)" role="img" aria-label="Isometric blue columns rising beneath the slogan letters"/>
    <polygon class="columns-shade" points="205,420 575,210 575,520 700,470 885,555 885,1200 205,1200" fill="var(--blue-deep)" opacity="0.25"/>
    <circle class="glow" cx="494" cy="401" r="363" fill="var(--blue-bright)" opacity="0.18"/>
    <circle class="glow-lower" cx="647" cy="1022" r="140" fill="var(--blue-bright)" opacity="0.45"/>

    <circle class="badge badge-automation" cx="784" cy="291" r="140" fill="#0563e6" role="img" aria-label="Robotic hand drawing with a pencil"/>
    <circle class="badge badge-mind" cx="107" cy="1068" r="80" fill="var(--blue-sky)" role="img" aria-label="Head profile with circuit brain icon"/>
    <path d="M40 1100 A80 80 0 0 1 40 990" fill="none" stroke="#ffd6dc" stroke-width="3" opacity="0.7"/>
    <path d="M125 966 A110 110 0 0 1 193 1006" fill="none" stroke="var(--blue-sky)" stroke-width="3"/>

    <!-- slogan -->
    <g class="slogan">
      <text class="slogan-elevate" font-size="270" textLength="420" lengthAdjust="spacingAndGlyphs"
            transform="matrix(0.866 -0.5 0.866 0.5 209 417)">ELEVATE</text>
      <text class="slogan-your" font-size="72" textLength="115" lengthAdjust="spacingAndGlyphs"
            transform="matrix(0.866 -0.5 0.866 0.5 338 545)">YOUR</text>
      <text class="slogan-expectations" font-size="270" textLength="724" lengthAdjust="spacingAndGlyphs"
            transform="matrix(0.866 -0.5 0.866 0.5 209 945)">EXPECTATIONS</text>
    </g>
  </svg>
</main>
</body>
</html>
```